Quiet Harbor Prints gallery website

I need a Website for a gallery with a shopify integration or maybe even better also compatible with squarespace.
the website should have following riders: Künstler, Veranstaltungen, Shop, About Us.
some nice examples for inspiration of the website architecture are:
https://www.lindwerkraum.com/
https://www.plattenbau-salon.com/de/
https://moorlichtraum.de/
It should be easy for us to make adaptations and fill the website with new content.
Attached there is the CI an logo for the brand.
Target Market(s)
Art Collectors,
Industry/Entity Type
artgallery
Coding
Coded - Design and coding required
Number of Pages Required
3 page
Font styles to use
Look and feel

```html
<!DOCTYPE html>
<html lang="en">
<head>
<meta charset="UTF-8">
<title>Quiet Harbor Prints</title>
<link href="https://fonts.googleapis.com/css2?family=Open+Sans:ital,wght@0,400;0,600;0,700;1,400&family=Raleway:wght@500;600;700&display=swap" rel="stylesheet">
<style>
:root{
  --red:#c8171e;
  --pink:#fde3e4;
  --grey:#eeeeee;
  --ink:#222222;
  --muted:#666666;
  --white:#ffffff;
  --black:#000000;
}
*{box-sizing:border-box;margin:0;padding:0}
html,body{width:1200px;height:3556px;overflow:hidden}
body{position:relative;font-family:"Open Sans",sans-serif;color:var(--ink);background:var(--white)}
.img{position:absolute;display:block}

/* header */
.site-header{position:absolute;left:0;top:0;width:1200px;height:72px;background:var(--white)}
.brand{position:absolute;display:flex;align-items:center;gap:10px}
.brand-mark{width:24px;height:24px;border:2px solid currentColor}
.brand-name{font-family:"Raleway",sans-serif;font-weight:600;letter-spacing:1px;text-transform:uppercase}
.site-header .brand{left:112px;top:20px;color:var(--ink)}
.site-header .brand-name{font-size:15px}
.main-nav{position:absolute;left:380px;top:22px;display:flex;gap:34px;font-size:14px;font-weight:600}
.main-nav a{color:var(--ink);text-decoration:none;padding-bottom:6px}
.main-nav a.active{border-bottom:2px solid var(--red)}
.hotline{position:absolute;left:800px;top:16px;display:flex;align-items:center;gap:12px}
.icon-circle{width:34px;height:34px;border-radius:50%;background:var(--grey);display:flex;align-items:center;justify-content:center}
.hotline small{display:block;font-size:10px;color:var(--muted);letter-spacing:1px}
.hotline strong{font-size:13px;color:var(--red);font-weight:600}
.header-icons{position:absolute;left:1010px;top:19px;display:flex;gap:12px}

/* hero */
.hero{position:absolute;left:0;top:72px;width:1200px;height:688px}
.hero-main{left:0;top:0;width:600px;height:688px;background:linear-gradient(180deg,#f7b32b 0%,#ef6b1f 38%,#d8452a 55%,#3c6fb5 78%,#1d3f7d 100%)}
.hero-title{position:absolute;left:128px;top:146px;font-family:"Raleway",sans-serif;font-weight:600;font-size:38px;color:var(--white);letter-spacing:1px}
.btn{display:inline-flex;align-items:center;gap:8px;background:var(--red);color:var(--white);font-size:12px;font-weight:700;text-transform:uppercase;text-decoration:none;height:40px;padding:0 22px}
.hero .btn{position:absolute;left:128px;top:250px}
.hero-top-left{left:600px;top:0;width:320px;height:348px;background:linear-gradient(160deg,#e9c9a0,#b56d5c 55%,#4a5e7a)}
.hero-top-right{left:920px;top:0;width:280px;height:348px;background:linear-gradient(180deg,#f0a040,#e14c3a 55%,#3a2f5a)}
.hero-bottom{left:600px;top:348px;width:600px;height:340px;background:linear-gradient(180deg,#e8ecf0,#c9cdd3 60%,#9aa1a8)}
.hero-frame{position:absolute;border:2px solid var(--red)}

/* section titles */
.section-title{position:absolute;left:0;width:1200px;text-align:center;font-family:"Raleway",sans-serif;font-weight:500;font-size:32px;color:var(--ink)}
.section-title::after{content:"";display:block;width:60px;height:2px;background:var(--red);margin:10px auto 0}

/* about */
.about-photo-a{left:112px;top:864px;width:368px;height:248px;background:linear-gradient(135deg,#c48a5a,#6b4a3a 60%,#2d2a2c)}
.about-photo-b{left:340px;top:1048px;width:240px;height:252px;background:linear-gradient(160deg,#7f8fa0,#3b4a5c);border:6px solid var(--white)}
.about-photo-c{left:236px;top:1128px;width:168px;height:176px;background:linear-gradient(180deg,#7aa7d6,#e3c3a1 60%,#5c7c4c);border:6px solid var(--white)}
.about-text{position:absolute;left:640px;top:880px;width:440px}
.about-text h2{font-family:"Raleway",sans-serif;font-weight:500;font-size:32px}
.about-text h2::after{content:"";display:block;width:60px;height:2px;background:var(--red);margin-top:8px}
.about-text p{font-size:13px;line-height:24px;color:var(--muted);margin-top:18px}
.about-text .btn{margin-top:30px}

/* events */
.events{position:absolute;left:0;top:1388px;width:1200px;height:564px;background:var(--grey)}
.card{position:absolute;background:var(--white);padding:12px;box-shadow:0 10px 18px rgba(0,0,0,.25)}
.card .fill{width:100%;height:100%}
.arrow{position:absolute;width:40px;height:40px;border-radius:50%;background:var(--red);display:flex;align-items:center;justify-content:center}

/* artists */
.artists{position:absolute;left:0;top:1960px;width:1200px;height:600px;background:var(--pink)}
.artist-card{position:absolute;width:280px;height:340px}
.artist-card .frame{position:absolute;left:16px;top:-16px;width:280px;height:250px;border:2px solid var(--red)}
.artist-card .photo{position:absolute;left:0;top:0;width:280px;height:250px}
.artist-card .name{position:absolute;left:0;top:250px;width:280px;height:90px;background:var(--white);text-align:center;padding-top:22px}
.artist-card h3{font-size:15px;font-weight:700;letter-spacing:1px;text-transform:uppercase}
.artist-card span{display:block;font-size:12px;font-style:italic;color:var(--red);margin-top:6px}

/* footer */
.site-footer{position:absolute;left:0;top:3180px;width:1200px;height:376px;background:var(--black);color:var(--white)}
.site-footer .brand{left:0;width:1200px;top:30px;flex-direction:column;gap:8px;color:var(--white)}
.site-footer .brand-mark{width:40px;height:40px}
.site-footer .brand-name{font-size:15px}
.footer-col{position:absolute;top:178px;font-size:11px;line-height:22px}
.footer-col h4{font-size:11px;font-weight:700;text-transform:uppercase;margin-bottom:10px;letter-spacing:.5px}
.footer-col p{color:#dddddd}
.social{position:absolute;top:190px;left:532px;display:flex;gap:22px}
.social span{width:30px;height:30px;border-radius:50%;background:var(--white)}
.copyright{position:absolute;left:0;top:328px;width:1200px;text-align:center;font-size:11px}
</style>
</head>
<body>

<header class="site-header">
  <div class="brand"><span class="brand-mark"></span><span class="brand-name">Quiet Harbor Prints</span></div>
  <nav class="main-nav">
    <a class="active" href="#">Home</a><a href="#">Artists</a><a href="#">Events</a><a href="#">Shop</a><a href="#">About Us</a>
  </nav>
  <div class="hotline">
    <span class="icon-circle"><svg width="14" height="14" viewBox="0 0 24 24"><path d="M6.6 10.8a15 15 0 006.6 6.6l2.2-2.2a1 1 0 011-.25 11.4 11.4 0 003.6.57 1 1 0 011 1V20a1 1 0 01-1 1A17 17 0 013 4a1 1 0 011-1h3.5a1 1 0 011 1 11.4 11.4 0 00.57 3.6 1 1 0 01-.25 1z" fill="#222"/></svg></span>
    <div><small>HOT LINE</small><strong>+1 (000) 000 000</strong></div>
  </div>
  <div class="header-icons">
    <span class="icon-circle"><svg width="14" height="14" viewBox="0 0 24 24"><path d="M3 4h3l2.4 11h10.2L21 7H7" fill="none" stroke="#222" stroke-width="2"/><circle cx="10" cy="19" r="1.6" fill="#222"/><circle cx="17" cy="19" r="1.6" fill="#222"/></svg></span>
    <span class="icon-circle"><svg width="14" height="14" viewBox="0 0 24 24"><circle cx="12" cy="8" r="4" fill="#222"/><path d="M4 21a8 8 0 0116 0z" fill="#222"/></svg></span>
  </div>
</header>

<section class="hero">
  <div class="img hero-main" role="img" aria-label="Painting of a wooden boat on a sunset-lit orange and blue sea"></div>
  <h1 class="hero-title">QUIET HARBOR PRINTS</h1>
  <a class="btn" href="#">Buy Now <svg width="12" height="12" viewBox="0 0 24 24"><circle cx="12" cy="12" r="11" fill="#fff"/><path d="M10 7l5 5-5 5" stroke="#c8171e" stroke-width="2.5" fill="none"/></svg></a>
  <div class="img hero-top-left" role="img" aria-label="Impressionist painting of people walking in a colourful street"></div>
  <div class="img hero-top-right" role="img" aria-label="Painting of a red autumn tree on a hillside at dusk"></div>
  <div class="img hero-bottom" role="img" aria-label="Bright gallery hall with framed paintings on white walls"></div>
  <div class="hero-frame" style="left:598px;top:0;width:604px;height:690px"></div>
  <div class="hero-frame" style="left:598px;top:346px;width:604px;height:2px;border-width:1px"></div>
</section>

<section class="about">
  <div class="img about-photo-a" role="img" aria-label="Artist painting on a canvas in a studio"></div>
  <div class="img about-photo-b" role="img" aria-label="Painter working at an easel"></div>
  <div class="img about-photo-c" role="img" aria-label="Landscape painting with sky and trees"></div>
  <div class="about-text">
    <h2>About Us</h2>
    <p>Lorem ipsum dolor sit amet, consectetur adipiscing elit, sed do eiusmod tempor incididunt ut labore et dolore magna aliqua. Ut enim ad minim veniam, quis nostrud exercitation ullamco laboris nisi ut aliquip ex ea commodo consequat.</p>
    <p>Lorem ipsum dolor sit amet, consectetur adipiscing elit, sed do eiusmod tempor incididunt ut labore et dolore magna aliqua. Ut enim ad minim veniam, quis nostrud exercitation ullamco laboris nisi ut aliquip ex ea commodo consequat. Duis aute irure dolor in reprehenderit in voluptate.</p>
    <a class="btn" href="#">Read More <svg width="12" height="12" viewBox="0 0 24 24"><circle cx="12" cy="12" r="11" fill="#fff"/><path d="M10 7l5 5-5 5" stroke="#c8171e" stroke-width="2.5" fill="none"/></svg></a>
  </div>
</section>

<section class="events">
  <h2 class="section-title" style="top:86px">Our Events</h2>
  <div class="card" style="left:112px;top:192px;width:288px;height:292px"><div class="fill" role="img" aria-label="Event photo of an artist painting at an easel" style="background:linear-gradient(135deg,#e6d6c0,#9a7a5a 55%,#4d5a6a)"></div></div>
  <div class="card" style="left:456px;top:192px;width:288px;height:292px"><div class="fill" role="img" aria-label="Exhibition wall with red framed paintings and a visitor" style="background:linear-gradient(180deg,#f2f2f2,#e0dcdc 50%,#c23a3a 52%,#e6e2e2 70%,#d0cccc)"></div></div>
  <div class="card" style="left:800px;top:192px;width:288px;height:292px"><div class="fill" role="img" aria-label="Visitor viewing large paintings in a white gallery room" style="background:linear-gradient(160deg,#dfe5ea,#8a9bb0 55%,#d4d8dc)"></div></div>
  <span class="arrow" style="left:40px;top:308px"><svg width="14" height="14" viewBox="0 0 24 24"><path d="M15 5l-7 7 7 7" stroke="#fff" stroke-width="3" fill="none"/></svg></span>
  <span class="arrow" style="left:1120px;top:308px"><svg width="14" height="14" viewBox="0 0 24 24"><path d="M9 5l7 7-7 7" stroke="#fff" stroke-width="3" fill="none"/></svg></span>
</section>

<section class="artists">
  <h2 class="section-title" style="top:94px">Our Artist</h2>
  <div class="artist-card" style="left:120px;top:176px"><div class="frame"></div><div class="photo" role="img" aria-label="Portrait photo of the artist" style="background:linear-gradient(180deg,#a0a4a8,#4a5660)"></div><div class="name"><h3>Milo Brandt</h3><span>Senior Artist</span></div></div>
  <div class="artist-card" style="left:460px;top:176px"><div class="frame"></div><div class="photo" role="img" aria-label="Portrait photo of the artist" style="background:linear-gradient(180deg,#d8d4cc,#5c6a3e)"></div><div class="name"><h3>Ilse Varga</h3><span>Senior Artist</span></div></div>
  <div class="artist-card" style="left:800px;top:176px"><div class="frame"></div><div class="photo" role="img" aria-label="Portrait photo of the artist" style="background:linear-gradient(180deg,#7c8a96,#e2b43a)"></div><div class="name"><h3>Nora Keel</h3><span>Senior Artist</span></div></div>
  <span class="arrow" style="left:40px;top:324px"><svg width="14" height="14" viewBox="0 0 24 24"><path d="M15 5l-7 7 7 7" stroke="#fff" stroke-width="3" fill="none"/></svg></span>
  <span class="arrow" style="left:1120px;top:324px"><svg width="14" height="14" viewBox="0 0 24 24"><path d="M9 5l7 7-7 7" stroke="#fff" stroke-width="3" fill="none"/></svg></span>
</section>

<section class="gallery">
  <h2 class="section-title" style="top:2650px">Our Gallery</h2>
  <div class="img" role="img" aria-label="Painting of snowy mountains with warm autumn colours" style="left:112px;top:2732px;width:396px;height:360px;background:linear-gradient(180deg,#a9c8e0,#e7e3dc 35%,#c9782f 65%,#7a3a1e)"></div>
  <div class="img" role="img" aria-label="Monochrome sketch of a figure on a balcony above a city" style="left:516px;top:2732px;width:280px;height:188px;background:linear-gradient(180deg,#f1f1f1,#9c9c9c)"></div>
  <div class="img" role="img" aria-label="Painting of palm trees against an orange sunset" style="left:516px;top:2928px;width:280px;height:164px;background:linear-gradient(180deg,#f5a14a,#e0582c 55%,#3b1a2a)"></div>
  <div class="img" role="img" aria-label="Painting of figures in a warm landscape" style="left:804px;top:2732px;width:284px;height:128px;background:linear-gradient(160deg,#d9b27a,#8a5a3a)"></div>
  <div class="img" role="img" aria-label="Colourful painting of a city skyline reflected in water" style="left:804px;top:2868px;width:284px;height:224px;background:linear-gradient(180deg,#b7d3e8,#e9c07a 50%,#6a92b8)"></div>
</section>

<footer class="site-footer">
  <div class="brand"><span class="brand-mark"></span><span class="brand-name">Quiet Harbor Prints</span></div>
  <div class="footer-col" style="left:112px"><h4>Shopping Help</h4><p>FAQs<br>Terms &amp; Conditions<br>Privacy Policy<br>Disclaimers<br>Print Assurance<br>Payment Options</p></div>
  <div class="footer-col" style="left:312px"><h4>Quick Links</h4><p>Gallery Services<br>Past Shows<br>Testimonials</p></div>
  <div class="social"><span></span><span></span><span></span></div>
  <div class="footer-col" style="left:760px"><h4>Location</h4><p>Lorem ipsum dolor sit<br>amet, consectetur<br>adipiscing elit, sed diup.</p></div>
  <div class="footer-col" style="left:960px"><h4>Contact</h4><p>+1 (000) 000 000<br>info@quietharborprints.com</p></div>
  <p class="copyright">Copyright©2024. All Rights Reserved By Quiet Harbor Prints.com</p>
</footer>

</body>
</html>
```